Tour operator needs simple coded WordPress site (updated extra payment for coding and guaranteed)

[update 9/7/2015]
If you design a new logo and it gets accepted, even if we use another template with your logo you will get $50
[update 8/7/2015]
Update on questions about dual-language
For dual languages we are happy to set up a second site with the same designs in a second language.
For the design aspect just allow the user to switch between languages with an icon.
For the coding, a replica of the site on a second server will do (to save messing around with multiple language plugins) - we will populate it with Chinese text
[original post]
Simple coded WordPress site for tours
You can choose to design only or design and code ($340 design, $150 bonus for coding)
Open design brief - use your creativity
Will be in 2 languages (English and Chinese) but design needs only to be in one language
Winning design will be chosen only from home page, but the winner must make a second standard template page when chosen at no extra cost.
Must be responsive design
We only need homepage and standard template page design and coding, we will populate the pages
You can use design ideas from our pamphlet if you like - attached
Only a sample logo and colors on website and pamphlet - feel free to change as the current ones seem restrictive
Current website framework only to give an idea of the number of pages and basic menu structure (no need to use existing navigation style or any style at all for that matter, open brief)
http://brightwattlejourneys.com.au/
Target Market(s)
Chinese parents of kids 10-14 (the kids will take the tour)
Industry/Entity Type
Tour
Number of Pages Required
2 page
Look and feel
Each slider illustrates characteristics of the customer's brand and the style your logo design should communicate.

```html
<!DOCTYPE html>
<html lang="en">
<head>
<meta charset="utf-8">
<title>Bright Wattle Journeys</title>
<link rel="stylesheet" href="https://fonts.googleapis.com/css2?family=Ubuntu:wght@400;500;700&family=Oswald:wght@500&family=Roboto:wght@400;500&display=swap">
<style>
:root{
  --navy:#2f3d80;
  --navy-deep:#27346e;
  --gold:#f5b01c;
  --ink:#2b2b2b;
  --text:#3a3a3a;
  --white:#ffffff;
  --rule:#cfcfcf;
}
*{box-sizing:border-box;margin:0;padding:0}
html,body{width:1200px;height:1048px;overflow:hidden;background:var(--white)}
body{position:relative;font-family:'Ubuntu',sans-serif;color:var(--text)}

.site-header{position:absolute;left:0;top:0;width:1200px;height:95px;background:var(--white)}
.lang-switch{position:absolute;left:160px;top:23px;width:117px;height:34px;background:var(--ink);border-radius:4px;
  color:var(--white);font:400 13px 'Roboto',sans-serif;display:flex;align-items:center;padding-left:18px;gap:8px}
.lang-switch .flag{width:20px;height:13px;background:#2a3f8f;border:1px solid #fff}
.lang-switch svg{margin-left:2px}
.book-now{position:absolute;left:950px;top:21px;width:88px;height:32px;background:var(--gold);border-radius:2px;
  color:var(--white);font:500 14px 'Ubuntu',sans-serif;display:flex;align-items:center;justify-content:center}

.main-nav{position:absolute;left:0;top:95px;width:1200px;height:42px;background:var(--navy)}
.main-nav a{position:absolute;top:0;height:42px;display:flex;align-items:center;justify-content:center;
  color:var(--white);font:500 15px 'Roboto',sans-serif;text-decoration:none;border-left:1px solid rgba(255,255,255,.15)}
.main-nav a.is-active{border-bottom:3px solid var(--gold)}
.main-nav .edge{position:absolute;top:0;width:1px;height:42px;background:rgba(255,255,255,.15)}

.brand{position:absolute;left:477px;top:0;width:246px;height:131px;background:var(--white);border-radius:0 0 6px 6px;
  box-shadow:0 2px 4px rgba(0,0,0,.15);display:flex;flex-direction:column;align-items:center;justify-content:center;gap:12px}
.brand .mark{width:44px;height:44px;border-radius:50%;background:var(--gold)}
.brand .name{font:500 15px 'Ubuntu',sans-serif;color:var(--navy);letter-spacing:.3px}

.hero{position:absolute;left:0;top:137px;width:1200px;height:419px;
  background:linear-gradient(90deg,#5c5134 0%,#6e6a45 25%,#4f5a33 50%,#7b7350 75%,#5a5a3a 100%)}
.hero-caption{position:absolute;left:160px;top:266px;width:500px;height:88px;background:rgba(40,40,40,.6);
  border-left:4px solid var(--gold);padding:10px 0 0 12px;overflow:hidden}
.hero-caption span{display:block;white-space:nowrap;transform:scaleX(.84);transform-origin:left center;
  color:var(--white);font:500 29px/34px 'Oswald',sans-serif;text-transform:uppercase}
.hero-arrow{position:absolute;top:208px}

.features{position:absolute;left:0;top:526px;width:1200px}
.feature{position:absolute;width:240px;text-align:center}
.feature .badge{width:136px;height:136px;border-radius:50%;background:var(--white);margin:0 auto;display:flex;align-items:center;justify-content:center}
.feature .label{margin-top:8px;font:500 16px 'Ubuntu',sans-serif;color:var(--ink)}
.feature.is-current .label{color:var(--navy)}
.divider{position:absolute;left:130px;top:719px;width:940px;height:2px;background:linear-gradient(90deg,transparent,#bdbdbd 20%,#bdbdbd 80%,transparent)}

.about{position:absolute;left:0;top:767px;width:1200px;text-align:center}
.about h2{font:500 28px 'Ubuntu',sans-serif;color:var(--navy)}
.about h2 .gold{color:var(--gold)}
.ornament{position:relative;width:630px;height:20px;margin:4px auto 0}
.ornament::before{content:"";position:absolute;left:0;right:0;top:9px;height:2px;background:linear-gradient(90deg,transparent,var(--rule) 30%,var(--rule) 70%,transparent)}
.ornament span{position:absolute;left:306px;top:0;width:18px;height:18px;border-radius:50%;background:var(--navy);border:4px solid var(--gold);box-shadow:0 0 0 3px #fff}
.about .lead{margin:13px auto 0;width:860px;font:500 13.5px/18px 'Ubuntu',sans-serif;color:var(--ink)}
.about .body{margin:12px auto 0;width:860px;font:400 13.5px/18px 'Ubuntu',sans-serif;color:#444}
.read-more{display:inline-block;margin-top:19px;width:105px;height:32px;background:var(--ink);border-radius:2px;
  color:var(--white);font:500 14px/32px 'Ubuntu',sans-serif}

.site-footer{position:absolute;left:0;top:1007px;width:1200px;height:41px;background:var(--navy)}
.site-footer p{position:absolute;left:160px;top:12px;color:var(--white);font:400 13px 'Ubuntu',sans-serif}
.social{position:absolute;top:1px;width:39px;height:39px;border-radius:50%;background:#d6dbe8;border:3px solid #fff}
</style>
</head>
<body>

<header class="site-header">
  <div class="lang-switch"><span class="flag"></span>English
    <svg width="10" height="7" viewBox="0 0 10 7"><path d="M1 1l4 4 4-4" fill="none" stroke="#fff" stroke-width="2"/></svg>
  </div>
  <div class="book-now">Book Now</div>
</header>

<nav class="main-nav">
  <a class="is-active" style="left:160px;width:139px">HOME</a>
  <a style="left:299px;width:149px">TOURS</a>
  <a style="left:751px;width:154px">CONTACT</a>
  <a style="left:905px;width:132px">ABOUT</a>
  <span class="edge" style="left:448px"></span>
  <span class="edge" style="left:1037px"></span>
</nav>

<div class="brand">
  <span class="mark"></span>
  <span class="name">BRIGHT WATTLE JOURNEYS</span>
</div>

<section class="hero" role="img" aria-label="Group of smiling students posing outdoors among trees">
  <svg class="hero-arrow" style="left:105px" width="20" height="30" viewBox="0 0 20 30"><path d="M16 2L4 15l12 13" fill="none" stroke="#fff" stroke-width="3"/></svg>
  <svg class="hero-arrow" style="left:1075px" width="20" height="30" viewBox="0 0 20 30"><path d="M4 2l12 13L4 28" fill="none" stroke="#fff" stroke-width="3"/></svg>
  <div class="hero-caption"><span>Educational, safe, culturally Australian</span><span>cultural exchange enlightening and fun.</span></div>
</section>

<section class="features">
  <div class="feature is-current" style="left:150px">
    <div class="badge">
      <svg width="122" height="122" viewBox="0 0 122 122">
        <circle cx="61" cy="61" r="58" fill="none" stroke="#2f3d80" stroke-width="2.5"/>
        <circle cx="61" cy="61" r="52" fill="#2f3d80"/>
        <path d="M61 34l34 14-34 14-34-14z" fill="#fff"/>
        <path d="M44 56v14c0 6 34 6 34 0V56l-17 7z" fill="#fff"/>
        <path d="M88 51v18" stroke="#fff" stroke-width="2.5"/>
      </svg>
    </div>
    <div class="label">Educational And Cultural</div>
  </div>
  <div class="feature" style="left:477px">
    <div class="badge">
      <svg width="122" height="122" viewBox="0 0 122 122">
        <circle cx="61" cy="61" r="58" fill="none" stroke="#f5b01c" stroke-width="2.5"/>
        <circle cx="61" cy="61" r="52" fill="#f5b01c"/>
        <path d="M61 30c9 6 18 8 27 8v22c0 16-12 26-27 32-15-6-27-16-27-32V38c9 0 18-2 27-8z" fill="#fff"/>
        <path d="M47 60l10 10 19-21" fill="none" stroke="#f5b01c" stroke-width="7" stroke-linecap="round" stroke-linejoin="round"/>
      </svg>
    </div>
    <div class="label">Safe And Secure</div>
  </div>
  <div class="feature" style="left:805px">
    <div class="badge">
      <svg width="122" height="122" viewBox="0 0 122 122">
        <circle cx="61" cy="61" r="58" fill="none" stroke="#f5b01c" stroke-width="2.5"/>
        <circle cx="61" cy="61" r="52" fill="#f5b01c"/>
        <circle cx="68" cy="64" r="22" fill="none" stroke="#fff" stroke-width="3"/>
        <path d="M46 64h44M68 42v44M54 50c9 6 19 6 28 0M54 78c9-6 19-6 28 0" fill="none" stroke="#fff" stroke-width="2.5"/>
        <path d="M28 58l40-8 4 4-40 12z" fill="#fff"/>
        <path d="M36 52l6-12 5 2-3 12z" fill="#fff"/>
      </svg>
    </div>
    <div class="label">Travel insurance</div>
  </div>
</section>

<div class="divider"></div>

<section class="about">
  <h2><span class="gold">ABOUT</span> BRIGHT <span class="gold">WATTLE</span> JOURNEYS</h2>
  <div class="ornament"><span></span></div>
  <p class="lead">At Bright Wattle Journeys We Are Passionate About Educational Travel And Opportunities For Students To Gain Academic And Cultural Understanding Of Australia.</p>
  <p class="body">14 day premium cultural and educational tours to Australian cities. Educational, safe, culturally enlightening and fun. Learn about educational institutions, history, sports, laws and customs, food and culture while improving your English.</p>
  <a class="read-more">READ MORE</a>
</section>

<footer class="site-footer">
  <p>© 2015&nbsp; BRIGHT WATTLE JOURNEYS. All Rights Reserved.</p>
  <span class="social" style="left:907px" aria-label="Social link"></span>
  <span class="social" style="left:953px" aria-label="Social link"></span>
  <span class="social" style="left:999px" aria-label="Social link"></span>
</footer>

</body>
</html>
```